Business cards to launch an education platform

Hi,
I am looking at having new business cards designed.
I am a startup, developing a web platform for schools and university, the education world. It's an online assessment system.
I would like a card that looks classy, and that is using the colors and the font of my logo.

I have attached:
1) my logo
2) A business card that I have designed quickly so you can have all the information required in the card, but I really don't like it.
3) The font that I am using (Lato Regular) to design my web platform
4) Some screenshots of my web platform so you can have a look at the style that I have.

Target Market(s)

Major market: Education system: Schools and university
Minor markets: Business in general

Industry/Entity Type

Business

Contact Information for Business Card

Clara Fenwick
Director

M: 0437 518 902
E: clara.fenwick@amberLoomSystems.com.au

Requirements
Must have
• The colors of my logo

```html
<!DOCTYPE html>
<html lang="en">
<head>
<meta charset="utf-8">
<title>Amber Loom Systems – Business Cards</title>
<link rel="stylesheet" href="https://fonts.googleapis.com/css2?family=Lato:wght@300;400;700;900&display=swap">
<style>
  :root {
    --page-bg: #eceef1;
    --sky: #2ab5e8;
    --sky-light: #4cc3ef;
    --navy: #14508f;
    --navy-deep: #0f3f78;
    --ink: #163d6e;
    --white: #ffffff;
    --card-shadow: 0 12px 30px rgba(20, 40, 70, 0.18);
  }
  * { box-sizing: border-box; margin: 0; padding: 0; }
  html, body {
    width: 1200px;
    height: 950px;
    overflow: hidden;
    background: var(--page-bg);
    font-family: "Lato", sans-serif;
  }
  .canvas {
    position: relative;
    width: 1200px;
    height: 950px;
  }
  .card {
    position: absolute;
    width: 690px;
    height: 420px;
    box-shadow: var(--card-shadow);
    overflow: hidden;
  }

  /* Back of card */
  .card--back {
    left: 90px;
    top: 40px;
    background: var(--sky);
    color: var(--white);
  }
  .back-brand {
    position: absolute;
    left: 0; right: 0;
    top: 120px;
    display: flex;
    flex-direction: column;
    align-items: center;
    gap: 22px;
  }
  .brand-square {
    width: 58px;
    height: 58px;
    background: var(--white);
  }
  .back-brand .brand-name {
    font-size: 34px;
    font-weight: 400;
    letter-spacing: 3px;
    color: var(--white);
  }
  .back-website {
    position: absolute;
    left: 0; right: 0;
    bottom: 58px;
    text-align: center;
    font-size: 17px;
    font-weight: 400;
    letter-spacing: 2.5px;
  }

  /* Front of card */
  .card--front {
    left: 420px;
    top: 490px;
    background: var(--white);
  }
  .front-brand {
    position: absolute;
    left: 70px;
    top: 66px;
    display: flex;
    align-items: center;
    gap: 20px;
  }
  .front-brand .brand-square {
    width: 70px;
    height: 70px;
    background: var(--navy);
  }
  .front-brand .brand-name {
    font-size: 38px;
    font-weight: 400;
    letter-spacing: 2px;
    color: var(--navy);
  }
  .person {
    position: absolute;
    left: 300px;
    top: 176px;
    text-align: center;
    width: 200px;
  }
  .person-name {
    font-size: 20px;
    font-weight: 900;
    color: var(--ink);
    letter-spacing: 0.5px;
  }
  .person-role {
    margin-top: 4px;
    font-size: 14px;
    font-weight: 400;
    color: var(--sky);
    letter-spacing: 1.5px;
  }
  .contact-band {
    position: absolute;
    left: 0; right: 0; bottom: 0;
    height: 150px;
    background: linear-gradient(180deg, var(--navy) 0%, var(--navy-deep) 100%);
    border-top: 6px solid var(--sky-light);
  }
  .contact-list {
    position: absolute;
    left: 240px;
    top: 30px;
    list-style: none;
    color: var(--white);
    font-size: 17px;
    font-weight: 300;
  }
  .contact-item {
    display: flex;
    align-items: center;
    gap: 12px;
    height: 34px;
  }
  .contact-item--email { margin-top: 6px; }
  .contact-icon { width: 18px; height: 18px; flex: none; }
</style>
</head>
<body>
<main class="canvas">

  <section class="card card--back" aria-label="Card back">
    <div class="back-brand">
      <span class="brand-square"></span>
      <span class="brand-name">Amber Loom Systems</span>
    </div>
    <p class="back-website">www.amberLoomSystems.com.au</p>
  </section>

  <section class="card card--front" aria-label="Card front">
    <div class="front-brand">
      <span class="brand-square"></span>
      <span class="brand-name">Amber Loom Systems</span>
    </div>

    <div class="person">
      <p class="person-name">CLARA FENWICK</p>
      <p class="person-role">DIRECTOR</p>
    </div>

    <div class="contact-band">
      <ul class="contact-list">
        <li class="contact-item">
          <svg class="contact-icon" viewBox="0 0 18 18" aria-hidden="true">
            <rect x="4.5" y="1" width="9" height="16" rx="1.5" fill="none" stroke="#fff" stroke-width="1.6"/>
            <circle cx="9" cy="14" r="1" fill="#fff"/>
          </svg>
          <span>0437 518 902</span>
        </li>
        <li class="contact-item contact-item--email">
          <svg class="contact-icon" viewBox="0 0 18 18" aria-hidden="true">
            <rect x="1" y="4" width="16" height="11" fill="#fff"/>
            <path d="M1 4 L9 10 L17 4" fill="none" stroke="#14508f" stroke-width="1.4"/>
          </svg>
          <span>clara.fenwick@amberLoomSystems.com.au</span>
        </li>
      </ul>
    </div>
  </section>

</main>
</body>
</html>
```